A5 Patient Information Booklet (Chiropractic Clinic) 4-8 pages

Here’s a polished, professional rewrite of your full brief and content, with clearer structure, corrected language, and a premium tone:

---

**Project Title:** Premium Patient Information Brochure (Chiropractic & Wellness Clinic)

---

### **Overview**

We are a health and wellness clinic seeking a premium, high-end patient information brochure to provide following a patient’s initial consultation and first treatment.

The purpose of this booklet is to:

* Reinforce trust and professionalism
* Help patients understand what to expect next
* Encourage adherence to care recommendations
* Position the clinic as calm, expert-led, and results-driven

---

### **Format**

* 4–8 page booklet (A5 or similar size)
* Print-ready and digital versions required

---

### **Target Audience**

Patients who have just completed their initial consultation and may have begun treatment. They may already be experiencing physical or mental changes, so the brochure should guide, reassure, and educate them on what comes next.

---

### **Tone & Style**

* Premium, calm, and reassuring
* Modern wellness aesthetic (not overly clinical)
* Clean layout with minimal clutter
* Soft, neutral colour palette (whites, creams, muted greens, soft blues)
* Elegant typography (e.g. Montserrat / Lato)
* High-end, trustworthy, and professional feel

---

### **Key Messages**

#### 1. Listen to Your Body

Patients may feel different after treatment. Reassure them that this is normal and part of the healing process.

#### 2. Post-Treatment Advice

* Stay well hydrated
* Rest if needed
* Avoid overexertion if the body requires recovery

#### 3. Healing is a Journey (Core Concept)

A strong visual metaphor of a **“road to recovery”** or **journey** should be central to the design.

This journey should clearly illustrate three phases:

* **Phase 1: Initial Care (Weeks 1–6)**
Focus: Reducing pain/discomfort, calming the body, and initiating response to treatment

* **Phase 2: Corrective Care (Weeks 6–12)**
Focus: Addressing underlying issues, improving function, and creating lasting change

* **Phase 3: Wellness / Maintenance (Ongoing)**
Focus: Maintaining progress, preventing relapse, and supporting long-term wellbeing

**Important:**

* Emphasise that this is not a quick fix
* Progress requires time and consistency
* Each patient follows an individualised care plan
* The journey should feel structured, positive, and achievable

#### 4. Personalised Care

Reinforce that every treatment plan is tailored specifically to the individual.

#### 5. Professional Reassurance

Patients should feel confident they are in expert hands and supported throughout their journey.

---

### **Design Direction**

* Use imagery that reflects calmness, progression, and wellness (e.g. pathways, nature, soft gradients)
* Avoid generic stock imagery
* **Only use original clinic images from website and social media**
* Prioritise white space and clarity
* Aim for a luxury spa/medical hybrid aesthetic

---

## **Content Structure (Page-by-Page)**

### **Front Cover**

* Clean, minimal, premium design
* Clinic branding

---

### **Page 1: Patient Case Summary**

**Title:** *Welcome to Fernwell Spine Studio*

Thank you for choosing Fernwell Spine Studio.

This booklet is designed to guide you through:

* What we found during your initial consultation
* Your personalised recommended treatment plan
* Your road to recovery
* Long-term wellness care
* Why we take the approach we do

---

### **Page 2: Your Care Journey**

**Stage 1: Your Initial Consultation**

Today we completed a comprehensive assessment of your health and function, including:

* Full case history and discussion of your symptoms and goals
* Orthopaedic and neurological testing
* Postural and movement assessment
* Initial treatment (where appropriate)

**What this tells us:**

* How your body is currently functioning
* Where areas of stress or dysfunction may be present
* The most appropriate and effective path forward for your care

---

### **Page 3: Your Suggested Treatment Plan**

Based on today’s findings, your recommended care plan is:

**______ treatments over ______ weeks**

This should be viewed alongside your *Road to Recovery* to help you understand what to expect.

We have also discussed:

* Expected timelines for improvement
* Available payment options

**After Treatment:**
It is common to feel different following treatment. This is a normal response as your body begins to adapt and respond.

We recommend:

* Staying well hydrated
* Allowing time for rest and recovery
* Avoiding overexertion if your body feels it needs it

---

### **Page 4: What to Expect Next**

Healing is not always linear—it is a process that occurs over time.

Your care will typically progress through the following stages:

* **Relief Care**
Focused on reducing discomfort and calming the body

* **Corrective Care**
Focused on addressing underlying issues and improving function
(This phase may include prescribed exercises)

* **Maintenance / Wellness Care**
Focused on sustaining progress, preventing recurrence, and supporting long-term health

---

### **Page 5: Understanding Chiropractic Care**

**What is Chiropractic?**
Chiropractic care focuses on the relationship between the spine, nervous system, and overall body function.

By improving spinal movement and alignment, chiropractic care helps support the nervous system, allowing the body to function and heal more effectively.

**About Fernwell Spine Studio**
At Fernwell Spine Studio, our approach is centred around personalised, patient-focused care. We aim to not only relieve symptoms but to address underlying causes and support long-term wellbeing.

---

### **Back Page**

* Clinic contact details
* Website
* Social media icons/handles

**Closing Message:**
“A healthier, stronger you—supported every step of the way.”

---

### **Deliverables**

* Print-ready PDF
* Editable source files

---

### **Additional Notes**

* The brochure should feel valuable and worth keeping
* Encourage long-term care in a subtle, non-pushy way
* Maintain clarity, readability, and strong visual hierarchy
* Balance professionalism with warmth and approachability

---

If you’d like, I can also turn this into **actual brochure copy (fully written, patient-facing text)** or help you refine it further for a designer.

Existing patients who want to feel better and look after themselves that is given after their initil consultation appointment

Chiropractic, wellness, health

• Montserrat or Lato

0094D4
00A9DD
6FCCEA
C7EBF8
E9F6FB
00AB8E
00BBA5
67D7C9
C6EFE9
E9F9F6
6B429C
8869AF
B7A5CE
E3DAEB
F3F0F8

• my own photos, look premium wellness, be clear and simple to understand for patients journey or what to expect next and over time
• USe my social media/website for ideas
• generic photos and images

```html
<!DOCTYPE html>
<html lang="en">
<head>
<meta charset="utf-8">
<title>Fernwell Spine Studio – Patient Booklet</title>
<link href="https://fonts.googleapis.com/css2?family=Montserrat:wght@400;500;600;700;800&display=swap" rel="stylesheet">
<style>
:root{
  --stage:#666666;
  --teal:#00a99d;
  --teal-dark:#00897f;
  --teal-soft:#67d7c9;
  --ink:#231f20;
  --text:#3a3a3a;
  --pink:#f783c6;
  --lilac:#b7a5ce;
  --blue:#6db3e6;
  --white:#ffffff;
  --photo-warm:#b9a896;
  --photo-teal:#2f9d97;
}
*{box-sizing:border-box;margin:0;padding:0}
html,body{width:1200px;height:2879px;overflow:hidden;background:var(--stage)}
body{position:relative;font-family:'Montserrat',sans-serif;color:var(--text)}
.photo{position:absolute}
/* ---------- cover spread ---------- */
.cover{position:absolute;left:103px;top:62px;width:981px;height:693px;overflow:hidden;background:var(--white)}
.cover svg.cover-shapes{position:absolute;left:0;top:0}
.closing{position:absolute;left:41px;top:424px;width:230px}
.closing h3{color:var(--teal);font-size:16px;font-weight:800;letter-spacing:.2px}
.closing p{color:var(--ink);font-size:16.5px;font-weight:700;line-height:1.2;margin-top:2px}
.cover-name{position:absolute;left:265px;top:462px;width:290px;text-align:center;color:var(--ink);font-size:19px;font-weight:600;line-height:1.2}
.contact{position:absolute;left:41px;top:540px;width:240px}
.contact .name{color:var(--ink);font-size:14px;font-weight:700}
.contact .sub{color:var(--teal);font-size:12.5px;font-weight:500;margin-bottom:6px}
.contact li{list-style:none;display:flex;align-items:center;gap:6px;font-size:11.5px;color:var(--ink);height:20px}
.contact .ico{width:13px;height:13px;border-radius:50%;background:var(--teal);flex:none}
.contact .ico.sq{border-radius:2px;background:#3b5998}
.contact .ico.sq2{border-radius:3px;background:#d6497f}
.map{position:absolute;left:273px;top:545px;width:174px;height:108px;border:2px solid var(--teal-soft);border-radius:10px;background:#eef7f6}
.cover-head{position:absolute;right:40px;top:502px;text-align:right;color:var(--ink);font-size:21px;font-weight:800;line-height:1.15}
.cover-intro{position:absolute;right:40px;top:556px;width:430px;text-align:right;color:var(--ink);font-size:12.5px;line-height:1.25}
.cover-url{position:absolute;right:42px;top:633px;width:310px;height:28px;border-radius:14px;background:#2b2326;color:var(--white);font-size:15px;font-weight:500;text-align:center;line-height:28px}
.logo-slot{position:absolute;left:752px;top:88px;width:200px;text-align:center;color:var(--ink);font-size:17px;font-weight:600;line-height:1.2}
/* ---------- inner pages ---------- */
.page{position:absolute;width:459px;height:652px;background:linear-gradient(180deg,var(--pink) 0%,var(--lilac) 50%,var(--blue) 100%)}
.card{position:absolute;left:26px;top:26px;right:26px;bottom:26px;background:var(--white);border-radius:12px;padding:22px 24px}
.card h1{color:var(--teal);font-size:25px;font-weight:800;line-height:1.15;letter-spacing:.3px}
.card h2{color:var(--teal);font-size:18px;font-weight:700;line-height:1.2}
.card h3{color:var(--teal);font-size:13.5px;font-weight:700;margin-top:14px}
.card .lead{color:var(--ink);font-size:20px;font-weight:700;line-height:1.22;margin-top:14px}
.card p{font-size:12.5px;line-height:1.3;color:var(--ink)}
.card .just{text-align:justify}
.ticks{list-style:none;margin-top:4px}
.ticks li{position:relative;padding-left:15px;font-size:12.5px;color:var(--ink);line-height:1.3;margin-bottom:8px}
.ticks li::before{content:"";position:absolute;left:0;top:4px;width:9px;height:9px;border-radius:50%;background:var(--teal)}
.ticks li::after{content:"";position:absolute;left:2.6px;top:5.8px;width:3px;height:4.5px;border:solid var(--white);border-width:0 1.3px 1.3px 0;transform:rotate(45deg)}
.ticks.tight li{margin-bottom:3px}
.ticks.two{display:grid;grid-template-columns:1fr 1fr;column-gap:10px}
.card .photo{left:24px;right:24px;border-radius:2px}
.blank{display:inline-block;border-bottom:1px solid var(--ink);width:115px}
.link{color:#2a7ec2;text-decoration:underline;font-weight:700}
.chart{border:4px solid #3a3a3a;background:linear-gradient(135deg,#f3f3f3,#fde7d2 50%,#d9efe4)}
/* treatment plan page: compact type */
.plan p,.plan .ticks li{font-size:11.5px;line-height:1.22}
.plan h3{font-size:12.5px;margin-top:9px}
.plan .ticks{margin-top:1px}
.plan .ticks li{margin-bottom:2px}
.plan .ticks li::before{top:3px}
.plan .ticks li::after{top:4.8px}
.plan .ticks.auto{grid-template-columns:auto 1fr;column-gap:14px}
.stage{display:flex;gap:12px;margin-top:10px}
.stage .badge{width:46px;height:46px;border-radius:50%;background:var(--teal);flex:none;position:relative}
.stage .badge::after{content:"";position:absolute;inset:5px;border-radius:50%;border:1.5px solid var(--white)}
.stage h4{color:var(--teal);font-size:12.5px;font-weight:700}
.stage p{font-size:12.5px;line-height:1.2}
.key{position:absolute;left:24px;top:20px;width:168px}
.key h2{color:var(--ink);font-size:18px;font-weight:800}
.key h5{display:flex;align-items:center;gap:5px;margin-top:12px;font-size:12px;color:#2a7ec2;font-weight:700;text-decoration:underline}
.key h5 .n{width:12px;height:13px;background:var(--ink);color:var(--white);font-size:10px;text-align:center;line-height:13px;text-decoration:none;flex:none}
.key p,.key li,.col-right p{font-size:9.5px;line-height:1.22;color:var(--text)}
.key .ticks li{font-size:9.5px;padding-left:12px;margin-bottom:2px}
.key .ticks li::before{width:7px;height:7px;top:2px}
.key .ticks li::after{left:2px;top:3.2px;width:2px;height:3.5px;border-width:0 1px 1px 0}
.key .ph{font-size:9px;font-weight:700;color:var(--teal);margin-top:8px}
.key .pt{font-size:9.5px;font-weight:700;color:var(--ink)}
.key .f b{color:var(--teal)}
.key .imp{color:var(--teal);font-size:10.5px;font-weight:700;margin-top:12px;text-decoration:underline}
.col-right{position:absolute;left:217px;top:445px;width:170px}
.col-right h5{display:flex;align-items:center;gap:5px;margin-top:10px;font-size:11px;color:var(--teal);font-weight:700;white-space:nowrap}
.col-right h5 .n{width:12px;height:13px;background:var(--ink);color:var(--white);font-size:10px;text-align:center;line-height:13px;flex:none}
</style>
</head>
<body>

<section class="cover">
  <svg class="cover-shapes" width="981" height="693" viewBox="0 0 981 693">
    <defs>
      <linearGradient id="pinkband" x1="0" y1="0" x2="0.3" y2="1">
        <stop offset="0" stop-color="#f086c6"/>
        <stop offset="1" stop-color="#a3a6e0"/>
      </linearGradient>
    </defs>
    <path d="M0 0 H520 C460 120 440 230 470 330 C350 400 200 300 0 340 Z" fill="var(--photo-teal)" role="img" aria-label="Teal-toned photo of a treatment couch"/>
    <path d="M505 0 H981 V300 C900 400 820 470 700 470 C600 470 520 510 480 560 C430 400 440 150 505 0 Z" fill="var(--photo-warm)" role="img" aria-label="Photo of the chiropractor treating a patient on a couch"/>
    <path d="M480 560 C520 510 600 470 700 470 C820 470 900 400 981 300 V693 H440 C450 640 460 600 480 560 Z" fill="url(#pinkband)"/>
    <circle cx="159" cy="256" r="117" fill="#c9b3a0" stroke="#fff" stroke-width="6" role="img" aria-label="Photo of the chiropractor giving a neck treatment"/>
    <circle cx="852" cy="98" r="128" fill="#fff"/>
    <circle cx="482" cy="410" r="90" fill="#c7a58e" stroke="#fff" stroke-width="6" role="img" aria-label="Portrait photo of the chiropractor"/>
  </svg>
  <div class="logo-slot">Fernwell Spine Studio</div>

  <div class="closing">
    <h3>CLOSING MESSAGE:</h3>
    <p>A healthier, stronger you — supported every step of the way.</p>
  </div>
  <div class="cover-name">Fernwell<br>Spine Studio</div>

  <div class="contact">
    <div class="name">Fernwell Spine Studio</div>
    <div class="sub">Chiropractic &amp; Wellness</div>
    <ul>
      <li><span class="ico"></span>12 Orchard Lane, Brookford BK4 7QT</li>
      <li><span class="ico"></span>hello@fernwellspine.co.uk</li>
      <li><span class="ico"></span>www.fernwellspine.co.uk</li>
      <li><span class="ico sq"></span><span class="ico sq2"></span>@fernwellspine_studio</li>
    </ul>
  </div>
  <div class="map" role="img" aria-label="Street map showing the clinic location"></div>

  <div class="cover-head">ALIGN YOUR BODY,<br>ELEVATE YOUR WELLBEING</div>
  <p class="cover-intro">At Fernwell Spine Studio Brookford, we offer personalised chiropractic care for adults &amp; families who want to feel their best — whether that's easing discomfort, improving movement, or supporting long-term wellbeing.</p>
  <div class="cover-url">www.fernwellspine.co.uk</div>
</section>

<section class="page" style="left:103px;top:800px">
  <div class="card">
    <h1>WELCOME TO<br>FERNWELL SPINE STUDIO</h1>
    <p class="lead">Thank you for<br>choosing Fernwell Spine Studio.</p>
    <h3 style="margin-top:16px">This booklet is designed to guide you through:</h3>
    <ul class="ticks" style="margin-top:6px">
      <li>What we found during your initial consultation</li>
      <li>Your personalised recommended treatment plan</li>
      <li>Your road to recovery</li>
      <li>Long-term wellness care</li>
      <li>Why we take the approach we do</li>
    </ul>
    <div class="photo" style="top:344px;height:229px;background:linear-gradient(160deg,#cfc8c0,#9d8f80)" role="img" aria-label="Photo of the clinic treatment room with the chiropractor"></div>
  </div>
</section>

<section class="page" style="left:625px;top:800px">
  <div class="card">
    <h2>YOUR CARE JOURNEY</h2>
    <p style="font-size:15px;font-weight:700;margin-top:6px">Stage 1:<br>Your Initial Consultation</p>
    <h3 style="margin-top:8px">Today we completed a comprehensive assessment of your health and function, including:</h3>
    <ul class="ticks tight" style="margin-top:4px">
      <li style="margin-bottom:7px">Full case history &amp; discussion of your symptoms &amp; goals</li>
      <li style="margin-bottom:7px">Orthopaedic and neurological testing</li>
      <li style="margin-bottom:7px">Postural and movement assessment</li>
      <li>Initial treatment (where appropriate)</li>
    </ul>
    <h3 style="margin-top:22px">WHAT THIS TELLS US:</h3>
    <ul class="ticks" style="margin-top:2px">
      <li>How your body is currently functioning</li>
      <li>Where areas of stress or dysfunction may be present</li>
      <li>The most appropriate and effective path forward for your care</li>
    </ul>
    <div class="photo" style="top:364px;height:209px;background:linear-gradient(160deg,#d9d6cf,#8f8578)" role="img" aria-label="Photo of the chiropractor assessing a patient lying on a couch"></div>
  </div>
</section>

<section class="page" style="left:103px;top:1487px">
  <div class="card plan">
    <h2>Your Suggested Treatment Plan</h2>
    <p style="margin-top:3px">Based on today's findings, your recommended care plan is:</p>
    <p style="margin-top:8px"><span class="blank"></span> treatments over<span class="blank" style="width:80px"></span> weeks</p>
    <p style="margin-top:12px;font-weight:700">This should be viewed alongside your <span class="link">*Road to Recovery*</span> to help you understand what to expect.</p>
    <h3>We have also discussed:</h3>
    <ul class="ticks two">
      <li>Expected timelines for improvement</li>
      <li>Available payment options</li>
    </ul>
    <h3>After Treatment:</h3>
    <p class="just">It is common to feel different following treatment. This is a normal response as your body begins to adapt and respond.</p>
    <h3>We recommend:</h3>
    <ul class="ticks two auto">
      <li>Staying well hydrated</li>
      <li>Allowing time for rest &amp; recovery</li>
    </ul>
    <ul class="ticks"><li>Avoiding overexertion if your body feels it needs it</li></ul>
    <div class="photo chart" style="top:326px;height:247px" role="img" aria-label="Road to Recovery chart showing healing, correction and maintenance phases over days, weeks, months and years"></div>
  </div>
</section>

<section class="page" style="left:625px;top:1487px">
  <div class="card">
    <h2>What to Expect Next</h2>
    <p style="font-size:13px">Healing is not always linear—it is a process that occurs over time.</p>
    <p style="font-weight:700;margin-top:14px;font-size:13px">Your care will typically progress through the following stages:</p>
    <div class="stage"><span class="badge"></span><div><h4>Relief Care</h4><p>Focused on reducing discomfort and calming the body</p></div></div>
    <div class="stage"><span class="badge"></span><div><h4>Corrective Care</h4><p>Focused on addressing underlying issues and improving function (This phase may include prescribed exercises)</p></div></div>
    <div class="stage"><span class="badge"></span><div><h4>Maintenance / Wellness Care</h4><p>Focused on sustaining progress, preventing recurrence, and supporting long-term health</p></div></div>
    <div class="photo" style="top:318px;height:255px;background:linear-gradient(160deg,#d6d2ca,#8b7f72)" role="img" aria-label="Photo of the chiropractor adjusting a patient's neck"></div>
  </div>
</section>

<section class="page" style="left:103px;top:2170px">
  <div class="card">
    <h2 style="color:var(--ink);margin-top:32px">Understanding Chiropractic Care</h2>
    <h3 style="margin-top:4px">What is Chiropractic?</h3>
    <p class="just">Chiropractic care focuses on the relationship between the spine, nervous system, and overall body function.</p>
    <p class="just" style="margin-top:12px">By improving spinal movement and alignment, chiropractic care helps support the nervous system, allowing the body to function and heal more effectively.</p>
    <h3 style="margin-top:16px">About Fernwell Spine Studio</h3>
    <p class="just">At Fernwell Spine Studio, our approach is centred around personalised, patient-focused care. We aim to not only relieve symptoms but to address underlying causes and support long-term wellbeing.</p>
    <div class="photo" style="top:300px;height:273px;background:linear-gradient(160deg,#c9c5bb,#8e8170)" role="img" aria-label="Photo of an empty clinic room with a treatment couch"></div>
  </div>
</section>

<section class="page" style="left:625px;top:2170px">
  <div class="card" style="padding:0">
    <div class="key">
      <h2>KEY MESSAGES:</h2>
      <h5 style="margin-top:2px"><span class="n">1</span>Listen to Your Body</h5>
      <p>Patients may feel different after treatment. Reassure them that this is normal and part of the healing process.</p>
      <h5><span class="n">2</span>Post-Treatment Advice</h5>
      <ul class="ticks">
        <li>Stay well hydrated</li>
        <li>Rest if needed</li>
        <li>Avoid overexertion if the body requires recovery</li>
      </ul>
      <h5 style="margin-top:14px"><span class="n">3</span>Healing is a Journey (Core Concept)</h5>
      <div class="ph">PHASE 1:</div><div class="pt">Initial Care (Weeks 1–6)</div>
      <p class="f"><b>Focus:</b> Reducing pain/discomfort, calming the body and helping you begin to respond to treatment.</p>
      <div class="ph" style="margin-top:12px">PHASE 2:</div><div class="pt">Corrective Care (Weeks 6–12)</div>
      <p class="f"><b>Focus:</b> Addressing underlying issues, improving function, and creating lasting change</p>
      <div class="ph" style="margin-top:12px">PHASE 3:</div><div class="pt">Wellness / Maintenance (Ongoing)</div>
      <p class="f"><b>Focus:</b> Maintaining progress, preventing relapse, and supporting long-term health and wellbeing.</p>
      <div class="imp">IMPORTANT:</div>
      <ul class="ticks" style="margin-top:4px">
        <li style="margin-bottom:7px">Emphasise that this is not a quick fix</li>
        <li style="margin-bottom:7px">Progress requires time, and consistency</li>
        <li style="margin-bottom:7px">Each patient follows an individualised care plan</li>
        <li>The journey should feel structured, positive and achievable</li>
      </ul>
    </div>
    <div class="photo" style="left:219px;right:auto;top:20px;width:162px;height:409px;background:linear-gradient(170deg,#e2e0db,#a7a2a0 60%,#7f8fae)" role="img" aria-label="Photo of the chiropractor treating a patient beside an anatomy chart"></div>
    <div class="col-right">
      <h5><span class="n">4</span>Personalised Care</h5>
      <p>Reinforce that every treatment plan is tailored specifically to the individual.</p>
      <h5 style="margin-top:12px"><span class="n">5</span>Professional Reassurance</h5>
      <p>Patients should feel confident that they are in expert hands and supported throughout their journey.</p>
    </div>
  </div>
</section>

</body>
</html>
```